Home Staging Company needs business card design

We're a home staging company called Brightly Settled Home Staging. We would like a business card design that includes aqua and gray. Our current logo of house within chair is fine but I find we almost always use the logo in one color. I'll upload images of front and back of our current card and our logo. Note that we have dropped "Solutions" from our company name and don't want to include it on the card.

Target Market(s)

Realtors and homeowners - people interested in selling their homes

Contact Information for Business Card

Marisol Thistlewood
Brightly Settled Home Staging
757-555-0193
www.brightlysettled.com
marisol@brightlysettled.com

Font styles to use
Serif
Script

Requirements
Must have
• My logo and contact details
• UPDATE***
• I forgot to say that the company name should be included on the front of the card somehow.

```html
<!DOCTYPE html>
<html lang="en">
<head>
<meta charset="utf-8">
<title>Brightly Settled Home Staging — Business Card</title>
<link rel="stylesheet" href="https://fonts.googleapis.com/css2?family=Playfair+Display:wght@400&family=Roboto:wght@400&family=Muli:wght@400&display=swap">
<style>
  :root {
    --backdrop: #b5b5b5;
    --aqua-light: #52b3ba;
    --aqua-deep: #1a88b0;
    --aqua-text: #3ea4b4;
    --card-white: #f4f4f4;
    --card-gray: #e6e6e6;
    --ink: #2f2f2f;
    --ink-soft: #3d3d3d;
    --paper-text: #ffffff;
  }
  * { margin: 0; padding: 0; box-sizing: border-box; }
  html, body { width: 1200px; height: 576px; overflow: hidden; }
  body {
    background: var(--backdrop);
    position: relative;
    font-family: "Roboto", Arial, sans-serif;
  }
  .card {
    position: absolute;
    top: 138px;
    height: 294px;
    border-radius: 12px;
    overflow: hidden;
  }
  .card-front {
    left: 82px;
    width: 484px;
    background: linear-gradient(180deg, var(--aqua-light) 0%, var(--aqua-deep) 100%);
    color: var(--paper-text);
  }
  .front-name {
    position: absolute;
    top: 112px;
    left: 0;
    right: 0;
    text-align: center;
    font-family: "Playfair Display", Georgia, serif;
    font-weight: 400;
    font-size: 32px;
    line-height: 1.15;
    color: var(--paper-text);
  }
  .front-url {
    position: absolute;
    top: 268px;
    left: 0;
    right: 0;
    text-align: center;
    font-family: "Muli", "Mulish", Arial, sans-serif;
    font-size: 13px;
    color: var(--paper-text);
  }
  .card-back {
    left: 602px;
    width: 480px;
    background: linear-gradient(160deg, var(--card-white) 0%, var(--card-gray) 100%);
    color: var(--ink);
  }
  .brand {
    position: absolute;
    top: 28px;
    left: 22px;
    display: flex;
    align-items: center;
    gap: 10px;
  }
  .brand-dot {
    width: 34px;
    height: 34px;
    border-radius: 50%;
    background: var(--aqua-text);
  }
  .brand-name {
    font-family: "Playfair Display", Georgia, serif;
    font-weight: 400;
    font-size: 18px;
    line-height: 1.1;
    color: var(--ink);
  }
  .person {
    position: absolute;
    top: 150px;
    left: 22px;
  }
  .person-name {
    font-size: 19px;
    color: var(--ink);
  }
  .person-name .surname { color: var(--aqua-text); }
  .person-title {
    margin-top: 5px;
    font-size: 11px;
    color: var(--ink-soft);
  }
  .contacts {
    position: absolute;
    top: 220px;
    left: 24px;
    list-style: none;
    font-family: "Muli", "Mulish", Arial, sans-serif;
    font-size: 12px;
    color: var(--ink-soft);
  }
  .contacts li {
    display: flex;
    align-items: center;
    gap: 12px;
    height: 17.5px;
  }
  .contacts svg { width: 10px; height: 10px; fill: var(--aqua-text); }
</style>
</head>
<body>
  <section class="card card-front" aria-label="Card front">
    <h1 class="front-name">Brightly Settled<br>Home Staging</h1>
    <p class="front-url">www.brightlysettled.com</p>
  </section>

  <section class="card card-back" aria-label="Card back">
    <div class="brand">
      <span class="brand-dot"></span>
      <span class="brand-name">Brightly Settled<br>Home Staging</span>
    </div>

    <div class="person">
      <p class="person-name">Marisol <span class="surname">Thistlewood</span></p>
      <p class="person-title">Managing Director</p>
    </div>

    <ul class="contacts">
      <li>
        <svg viewBox="0 0 10 10" aria-hidden="true"><path d="M1 3 Q5 0 9 3 L8 4.5 L6.5 3.8 L6.5 3 Q5 2.5 3.5 3 L3.5 3.8 L2 4.5 Z M2.5 5 H7.5 L8.5 9 H1.5 Z"/></svg>
        <span>757-555-0193</span>
      </li>
      <li>
        <svg viewBox="0 0 10 10" aria-hidden="true"><path d="M5 0.5 A4.5 4.5 0 1 0 5 9.5 A4.5 4.5 0 1 0 5 0.5 Z M5 1.6 Q6.6 3 6.6 5 Q6.6 7 5 8.4 Q3.4 7 3.4 5 Q3.4 3 5 1.6 Z M1.6 4.5 H8.4 V5.5 H1.6 Z" fill-rule="evenodd"/></svg>
        <span>www.brightlysettled.com</span>
      </li>
      <li>
        <svg viewBox="0 0 10 10" aria-hidden="true"><path d="M0.5 2 H9.5 V8 H0.5 Z M1.2 2.6 L5 5.4 L8.8 2.6 Z" fill-rule="evenodd"/></svg>
        <span>marisol@brightlysettled.com</span>
      </li>
    </ul>
  </section>
</body>
</html>
```